Dental Business Card Design w/logo

Classic, elegant w/a touch of contemporary
Upscale dental facility located in Modesto CA
Specializing in restorative & general dentistry
Providing exceptional customer service to the community
Updates

I prefer script and not bold writing
If you can use the phone; fax and email icons instead of spelling them out, it would be great
No bold colors
Classy and elegant
In the back of the card I would like to see something like this
Your Next Appointment:
Mon     Tue    Wed    Thur (a box next to each of them for marking)
Date:_______________ at_____________ AM    PM  (a box next to them for marking)

Thank you

Target Market(s)

Well established professional

Industry/Entity Type

Dental

Contact Information for Business Card

Velarina Tossudi DMD
4176 Marlow Rd
Suite K7
Modesto, CA 95418

Office: 209-731-5920
Fax: 209-731-8047
Email: tossudidmd@quillmail.example

Requirements
Must have
• Unique classic logo
An easily repeatable design that can be used on letterhead and envelopes
Nice to have
• My initials incorporated into unique design
Should not have
• No cartoons or cheesy themes. This is a practice for the well established and professional individual.

```html
<!DOCTYPE html>
<html lang="en">
<head>
<meta charset="utf-8">
<title>Velarina Tossudi, D.M.D. — Stationery</title>
<link rel="stylesheet" href="https://fonts.googleapis.com/css2?family=EB+Garamond:ital,wght@0,400;1,400&display=swap">
<style>
  :root {
    --backdrop: #272727;
    --paper: #ffffff;
    --paper-shade: #f3f3f3;
    --ink: #6b6b6b;
    --ink-soft: #8d8d8d;
    --teal: #8fd1cd;
    --teal-deep: #5fb3ae;
    --rule: #b9b9b9;
  }
  * { margin: 0; padding: 0; box-sizing: border-box; }
  html, body { width: 1200px; height: 1051px; overflow: hidden; }
  body {
    background: var(--backdrop);
    position: relative;
    font-family: "EB Garamond", Garamond, serif;
    color: var(--ink);
  }
  .sheet {
    position: absolute;
    background: var(--paper);
    box-shadow: 0 2px 10px rgba(0,0,0,.45);
  }
  .mark-dot {
    display: block;
    border-radius: 50%;
    background: var(--teal);
  }
  .practice-name {
    text-transform: uppercase;
    letter-spacing: .04em;
    color: var(--ink);
    white-space: nowrap;
  }
  .tagline {
    font-style: italic;
    color: var(--ink-soft);
    white-space: nowrap;
  }
  .small-lines { line-height: 1.25; white-space: nowrap; }
  .label { color: var(--teal-deep); }
  .email { color: var(--teal-deep); }

  /* Letterhead */
  .letterhead { left: 194px; top: 142px; width: 541px; height: 766px; }
  .letterhead .address {
    position: absolute; left: 22px; top: 24px; font-size: 6.5px;
  }
  .letterhead .identity {
    position: absolute; left: 0; right: 0; top: 24px; text-align: center;
  }
  .letterhead .mark-dot { width: 40px; height: 40px; margin: 0 auto 6px; }
  .letterhead .practice-name { font-size: 8px; }
  .letterhead .tagline { font-size: 7px; }
  .letterhead .email {
    position: absolute; left: 0; right: 0; bottom: 24px;
    text-align: center; font-size: 6.5px;
  }

  /* Envelope */
  .envelope {
    left: 452px; top: 446px; width: 553px; height: 279px;
    background: linear-gradient(180deg, var(--paper) 0%, var(--paper-shade) 100%);
  }
  .envelope .identity {
    position: absolute; left: 14px; top: 14px;
    display: flex; align-items: center; gap: 6px;
  }
  .envelope .mark-dot { width: 32px; height: 32px; }
  .envelope .practice-name { font-size: 11px; line-height: 1.1; }
  .envelope .tagline { font-size: 10.5px; }
  .envelope .return-address {
    position: absolute; right: 14px; bottom: 16px;
    text-align: right; font-size: 7.5px;
  }

  /* Appointment card (back) */
  .appointment-card { left: 782px; top: 144px; width: 139px; height: 238px; }
  .appointment-card .heading {
    position: absolute; left: 0; right: 0; top: 64px;
    text-align: center; font-size: 6.5px; letter-spacing: .03em;
  }
  .appointment-card .days {
    position: absolute; left: 16px; top: 83px;
    display: flex; gap: 8px; font-size: 5px;
  }
  .appointment-card .day { display: flex; align-items: center; gap: 2px; }
  .box { width: 4px; height: 4px; border: .6px solid var(--ink-soft); display: inline-block; }
  .appointment-card .field {
    position: absolute; left: 26px; font-size: 5px;
    display: flex; align-items: flex-end; gap: 3px;
  }
  .appointment-card .field .line { width: 70px; border-bottom: .6px dotted var(--rule); height: 5px; }
  .appointment-card .field.date { top: 100px; }
  .appointment-card .field.time { top: 115px; }
  .appointment-card .notice {
    position: absolute; left: 12px; right: 12px; top: 172px;
    font-size: 4.6px; font-style: italic; text-align: center; line-height: 1.3;
  }

  /* Business card (front) */
  .business-card { left: 864px; top: 181px; width: 139px; height: 236px; }
  .business-card .identity { position: absolute; left: 0; right: 0; top: 28px; text-align: center; }
  .business-card .mark-dot { width: 40px; height: 40px; margin: 0 auto 22px; }
  .business-card .practice-name { font-size: 6px; }
  .business-card .tagline { font-size: 5px; }
  .business-card .contact {
    position: absolute; left: 0; right: 0; top: 148px;
    text-align: center; font-size: 5px;
  }
  .business-card .contact .phones { margin-top: 8px; }
  .business-card .contact .email { margin-top: 6px; }
</style>
</head>
<body>

  <section class="sheet letterhead" aria-label="Letterhead">
    <div class="address small-lines">
      4176 Marlow Rd. Suite K7<br>
      Modesto, CA 95418<br>
      <span class="label">T:</span> 209 731 5920<br>
      <span class="label">F:</span> 209 731 8047
    </div>
    <div class="identity">
      <span class="mark-dot"></span>
      <div class="practice-name">Velarina Tossudi, D.M.D.</div>
      <div class="tagline">General &amp; Restorative Dentistry</div>
    </div>
    <div class="email">tossudidmd@quillmail.example</div>
  </section>

  <section class="sheet appointment-card" aria-label="Appointment card, back">
    <div class="heading">Your Next Appointment</div>
    <div class="days">
      <span class="day"><span class="box"></span>Mon.</span>
      <span class="day"><span class="box"></span>Tue.</span>
      <span class="day"><span class="box"></span>Wed.</span>
      <span class="day"><span class="box"></span>Thur.</span>
    </div>
    <div class="field date">Date: <span class="line"></span></div>
    <div class="field time">Time: <span class="line"></span></div>
    <p class="notice">If unable to keep this appointment, please give 48 hours notice, otherwise a charge will be made for time reserved.</p>
  </section>

  <section class="sheet business-card" aria-label="Business card, front">
    <div class="identity">
      <span class="mark-dot"></span>
      <div class="practice-name">Velarina Tossudi, D.M.D.</div>
      <div class="tagline">General &amp; Restorative Dentistry</div>
    </div>
    <div class="contact small-lines">
      <div>4176 Marlow Rd. Suite K7<br>Modesto, CA 95418</div>
      <div class="phones"><span class="label">T:</span> 209 731 5920<br><span class="label">F:</span> 209 731 8047</div>
      <div class="email">tossudidmd@quillmail.example</div>
    </div>
  </section>

  <section class="sheet envelope" aria-label="Envelope">
    <div class="identity">
      <span class="mark-dot"></span>
      <div>
        <div class="practice-name">Velarina Tossudi, D.M.D.</div>
        <div class="tagline">General &amp; Restorative Dentistry</div>
      </div>
    </div>
    <div class="return-address small-lines">
      4176 Marlow Rd. Suite K7<br>
      Modesto, CA 95418
    </div>
  </section>

</body>
</html>
```